Independent Financial Advisor Billboard Campaign - Maple Crest Financial

I am a local, independent financial advisor. My company is Maple Crest Financial, located in Charleston, WV. My main source of revenue comes from those nearing or entering retirement that need assistance with financial planning and investment management. Many are looking to rollover their employer retirement plan into an IRA account. I would like a billboard design campaign that focuses on this type of client. Please see our website www.maplecrestfinancial.com for more information.

```html
<!DOCTYPE html>
<html lang="en">
<head>
<meta charset="utf-8">
<title>Maple Crest Financial – Billboard</title>
<link href="https://fonts.googleapis.com/css2?family=Cinzel:wght@500&family=Oswald:wght@400&family=Montserrat:wght@400&display=swap" rel="stylesheet">
<style>
  :root {
    --navy: #3a5078;
    --navy-deep: #34496f;
    --paper: #f3f1f0;
    --mark-grey: #c9c9cb;
    --photo-light: #8f9bb2;
    --photo-mid: #6f7f9c;
    --page: #e6e7ea;
  }
  * { margin: 0; padding: 0; box-sizing: border-box; }
  html, body {
    width: 1200px; height: 733px; overflow: hidden;
    background: var(--page);
  }
  .billboard {
    position: absolute; left: 20px; top: 191px;
    width: 1160px; height: 350px;
    background: var(--navy);
    overflow: hidden;
  }
  .billboard__photo {
    position: absolute; right: 0; top: 0;
    width: 470px; height: 100%;
    background:
      radial-gradient(ellipse at 70% 40%, var(--photo-light) 0%, transparent 60%),
      linear-gradient(90deg, var(--navy) 0%, var(--photo-mid) 45%, var(--photo-light) 100%);
  }
  .brand {
    position: absolute; left: 40px; top: 55px;
    display: flex; align-items: center; gap: 70px;
  }
  .brand__square {
    width: 150px; height: 150px;
    background: var(--mark-grey);
    flex: none;
  }
  .brand__name {
    font-family: "Cinzel", serif; font-weight: 500;
    color: var(--paper);
    text-align: right;
  }
  .brand__line--main { display: block; font-size: 78px; line-height: 1; letter-spacing: 1px; }
  .brand__line--sub  { display: block; font-size: 38px; line-height: 1; letter-spacing: 30px; margin-top: 26px; margin-right: -30px; text-align: center; }
  .services {
    position: absolute; left: 996px; top: 80px;
    border-left: 2px solid var(--paper);
    padding-left: 18px; height: 190px;
    list-style: none;
    display: flex; flex-direction: column; justify-content: space-between;
    padding-top: 6px; padding-bottom: 6px;
    font-family: "Oswald", sans-serif; font-weight: 400; color: var(--paper);
    font-size: 18px; line-height: 1.2; letter-spacing: -0.2px;
    white-space: nowrap;
  }
  .contact-band {
    position: absolute; left: 0; bottom: 0;
    width: 985px; height: 72px;
    background: var(--paper);
    border-top-right-radius: 28px;
    display: flex; align-items: center;
    padding-left: 35px;
    font-family: "Montserrat", sans-serif; color: var(--navy-deep);
    font-size: 18px; letter-spacing: 0.3px;
    white-space: nowrap;
  }
  .contact-band__tagline { font-size: 21px; letter-spacing: 1.5px; margin-right: 6px; }
</style>
</head>
<body>
  <section class="billboard">
    <div class="billboard__photo" role="img" aria-label="Photo of a smiling retired couple embracing"></div>

    <div class="brand">
      <div class="brand__square"></div>
      <div class="brand__name">
        <span class="brand__line--main">Maple Crest</span>
        <span class="brand__line--sub">Financial</span>
      </div>
    </div>

    <ul class="services">
      <li>FINANCIAL ADVICE</li>
      <li>FINANCIAL PLANING</li>
      <li>INVESTMENTS</li>
      <li>INSURANCE</li>
      <li>EMPLOYER PLANS</li>
    </ul>

    <div class="contact-band">
      <span class="contact-band__tagline">YOUR FINANCIAL FUTURE/</span>
      <span class="contact-band__details">www.maplecrestfinancial.com/ hello@maplecrestfinancial.com</span>
    </div>
  </section>
</body>
</html>
```